Redesign company trifold brochure

We are rebranding our company in September and looking for a more professional design for our brochure.

What we do - providing interdisciplinary care for those supporting ill, elderly and special needs pets at home following the human hospice model of care - is very novel and our brochure is key in explaining it and our offerings.

We serve dogs and cats. Most of the animals are quite sick, elderly. I have many personal and stock photos we can use in the brochure. Please - no pictures of puppies and/or kittens.

The hard part is fitting the info and message into a clear and concise format.

It must be appealing both to pet owners and vets (who are our primary source of patients through referrals).

It should covey WARMTH, COMPASSION, PROFESSIONALISM, and EXPERTISE.

Please look at our website www.TrellisAnimalRespite.com for more info

We have until now used maroon and copper for colors - to reflect the "sunset" of the pets life. BUT are now changing to Navy, Teal and White to reflect calm, trust and competence.

We will use the same logo recolored.

Existing brochure and new logo are attached.

PLEASE ask questions!!
Updates

We have a library of stock images you are welcome to use. All have been legally acquired and we have the right to use them. You DO NOT have to use them, just sending along in case you wish to. https://www.filecrate.example/sh/qk4vrm82zd1pyno/KLQ7Ztbn-Rrfx2mh9sWpYJ4Dc?dl=0

Our colors are NAVY, TEAL and WHITE. For your reference, the navy we use is 99/87/44/55 (CMYK) The Teal we use is 76/11/44/0 (CMYK) Thank you!

Designers -- pleaseuse pictures of older pets (no puppies or kittens). Below is a link to stock photos we own that would be appropriate for use in the brochure. https://www.filecrate.example/sh/w274m6t9pxkr5da/KLRn3GsfwlTVBXEPcq_8ZNj5u?dl=0 THANK YOU!

Designers -- I would VERY much like to include a photo of a pet in a wheel chair. I have personal photos as well as (purchased) stock photos for this purpose which can be found at http://lnk.example/TARHC-Pets-in-Wheelchairs Thank you!!

Today is the last day! Many of you have submitted beautiful designs and others are rolling in. I am so appreciative of your time and energy!! Please do not let the deadline pass without YOUR very BEST entry being submitted!! Thank you! - Miriam & All of us at Trellis Animal Respite & Home Care

Target Market(s)

Pet Owners and Veterinarians

Industry/Entity Type

Pet Care

Font styles to use
Serif

Colors
0455a3
33b8a4
ffffff

Requirements
Must have
• Our logo and information about our services. Pictures of pets. Our contact info. PLEASE NOTE: this is a 2 sided brochure. Please submit both inside and outside.
Should not have
• puppies, kittens - anything off message

```html
<!DOCTYPE html>
<html lang="en">
<head>
<meta charset="utf-8">
<title>Trellis Animal Respite &amp; Home Care – Trifold Outside</title>
<link rel="stylesheet" href="https://fonts.googleapis.com/css2?family=Josefin+Sans:wght@700&family=Crimson+Text:wght@400;600&family=Parisienne&display=swap">
<style>
  :root {
    --navy: #0c2a4f;
    --teal: #3aa99b;
    --teal-soft: rgba(58, 169, 155, 0.82);
    --white: #ffffff;
    --paper: #f2f2f1;
    --ink: #3b3f44;
    --backdrop: #dcdcdc;
  }
  * { box-sizing: border-box; margin: 0; padding: 0; }
  html, body { width: 1200px; height: 800px; overflow: hidden; background: var(--backdrop); }
  .trifold {
    position: absolute; left: 60px; top: 50px;
    width: 1080px; height: 700px;
    display: flex;
    box-shadow: 0 10px 30px rgba(0,0,0,0.18);
  }
  .panel { position: relative; width: 360px; height: 700px; overflow: hidden; background: var(--white); }
  .panel--contact { background: var(--paper); }
  .panel-shapes { position: absolute; inset: 0; width: 360px; height: 700px; }
  .panel-title {
    position: absolute; top: 48px; width: 100%; text-align: center;
    font-family: "Josefin Sans", Arial, sans-serif; font-weight: 700;
    font-size: 25px; letter-spacing: 1.5px; color: var(--teal);
  }
  .beliefs { position: absolute; left: 28px; right: 22px; list-style: none; }
  .beliefs--upper { top: 150px; }
  .beliefs--lower { top: 590px; }
  .belief {
    display: flex; align-items: flex-start; gap: 10px;
    font-family: "Crimson Text", Georgia, serif; font-size: 14px; line-height: 1.15;
    color: var(--ink); margin-bottom: 18px;
  }
  .belief-number {
    flex: 0 0 22px; height: 22px; border-radius: 50%;
    background: var(--teal); color: var(--white);
    font-family: "Josefin Sans", Arial, sans-serif; font-weight: 700; font-size: 13px;
    display: flex; align-items: center; justify-content: center; padding-top: 2px;
  }
  .contact { position: absolute; top: 140px; width: 100%; text-align: center; font-family: "Crimson Text", Georgia, serif; color: var(--ink); }
  .contact-name { font-variant: small-caps; font-weight: 600; font-size: 17px; color: var(--navy); line-height: 1.15; margin-bottom: 12px; }
  .contact-address { font-size: 14px; line-height: 1.3; }
  .contact-phone { font-size: 23px; font-weight: 600; color: var(--teal); margin: 12px 0 10px; letter-spacing: 0.5px; }
  .contact-email { font-size: 14px; }
  .web { position: absolute; top: 438px; width: 100%; text-align: center; }
  .web-heading { font-family: "Josefin Sans", Arial, sans-serif; font-weight: 700; font-size: 24px; color: var(--navy); letter-spacing: 0.5px; }
  .web-address { font-family: "Crimson Text", Georgia, serif; font-size: 15px; color: var(--white); margin-top: 8px; letter-spacing: 0.3px; }
  .social { position: absolute; top: 578px; width: 100%; text-align: center; font-family: "Crimson Text", Georgia, serif; font-weight: 600; color: var(--navy); font-size: 16px; }
  .social-handle { display: flex; align-items: center; justify-content: center; gap: 8px; margin-bottom: 16px; }
  .social-marker { width: 14px; height: 14px; background: var(--navy); display: inline-block; }
  .brand-box {
    position: absolute; left: 70px; top: 250px; width: 260px; height: 104px;
    background: var(--navy); display: flex; align-items: center; justify-content: center; gap: 12px; padding: 0 18px;
  }
  .brand-dot { flex: 0 0 16px; height: 16px; border-radius: 50%; background: var(--teal); }
  .brand-name { font-family: "Crimson Text", Georgia, serif; font-size: 19px; line-height: 1.1; color: var(--white); }
  .tagline { position: absolute; top: 390px; width: 100%; text-align: center; font-family: "Crimson Text", Georgia, serif; font-size: 16px; color: var(--white); line-height: 1.3; }
  .script-line { position: absolute; top: 560px; right: 28px; text-align: center; font-family: "Parisienne", cursive; font-size: 27px; color: var(--navy); line-height: 1.1; }
</style>
</head>
<body>
<main class="trifold">

  <section class="panel panel--beliefs">
    <svg class="panel-shapes" viewBox="0 0 360 700">
      <defs>
        <linearGradient id="catTones" x1="0" y1="0" x2="1" y2="1">
          <stop offset="0" stop-color="#8a7a5c"/>
          <stop offset="0.5" stop-color="#6d8a3c"/>
          <stop offset="1" stop-color="#a4c25a"/>
        </linearGradient>
      </defs>
      <path d="M0 0H360V98Q180 132 0 122Z" fill="var(--navy)" aria-hidden="true"/>
      <path d="M0 436Q180 408 360 422V560Q180 584 0 572Z" fill="url(#catTones)" role="img" aria-label="Photo of a tabby cat resting in green grass"/>
    </svg>
    <h2 class="panel-title">WE BELIEVE</h2>
    <ol class="beliefs beliefs--upper">
      <li class="belief"><span class="belief-number">1</span><span>That animals are conscious beings, capable of thought, feeling, emotion and choice.</span></li>
      <li class="belief"><span class="belief-number">2</span><span>That each animal is an individual with his or her unique needs and wishes.</span></li>
      <li class="belief"><span class="belief-number">3</span><span>That all pets deserve to be pain-free.</span></li>
      <li class="belief"><span class="belief-number">4</span><span>That the principles of human hospice and palliative care are equally powerful when applied to animals.</span></li>
      <li class="belief"><span class="belief-number">5</span><span>That an interdisciplinary team is essential to addressing the needs of pets and their families through aging and illness.</span></li>
    </ol>
    <ol class="beliefs beliefs--lower">
      <li class="belief"><span class="belief-number">6</span><span>That quality of life is subjective, best evaluated by the family who knows and loves the animal.</span></li>
      <li class="belief"><span class="belief-number">7</span><span>That there isn’t one answer that is right for every animal or every family.</span></li>
    </ol>
  </section>

  <section class="panel panel--contact">
    <svg class="panel-shapes" viewBox="0 0 360 700">
      <defs>
        <linearGradient id="companionTones" x1="0" y1="0" x2="1" y2="0">
          <stop offset="0" stop-color="#c98a45"/>
          <stop offset="0.6" stop-color="#b57a3e"/>
          <stop offset="1" stop-color="#8d8478"/>
        </linearGradient>
      </defs>
      <path d="M0 0H360V98Q180 132 0 122Z" fill="var(--navy)" aria-hidden="true"/>
      <path d="M0 372Q190 336 360 298V520Q180 566 0 540Z" fill="var(--teal)" aria-hidden="true"/>
      <rect x="50" y="330" width="200" height="84" rx="36" fill="url(#companionTones)" role="img" aria-label="Photo of an older dog lying beside a cat"/>
    </svg>
    <h2 class="panel-title">CONTACT US</h2>
    <div class="contact">
      <p class="contact-name">Trellis Animal Respite<br>&amp; Home Care</p>
      <p class="contact-address">218 Meadowbrook Lane<br>Suite 40<br>Ashfield, MA 01330</p>
      <p class="contact-phone">(555) 302-TARH</p>
      <p class="contact-email">info@TrellisAnimalRespite.com</p>
    </div>
    <div class="web">
      <h3 class="web-heading">ON THE WEB</h3>
      <p class="web-address">www.TrellisAnimalRespite.com</p>
    </div>
    <div class="social">
      <p class="social-handle"><span class="social-marker"></span>TrellisRespite</p>
      <p class="social-handle"><span class="social-marker"></span>TrellisAnimalRespite</p>
    </div>
  </section>

  <section class="panel panel--cover">
    <svg class="panel-shapes" viewBox="0 0 360 700">
      <defs>
        <linearGradient id="coverPhoto" x1="0" y1="0" x2="0" y2="1">
          <stop offset="0" stop-color="#4f7a3a"/>
          <stop offset="0.35" stop-color="#c08a45"/>
          <stop offset="0.75" stop-color="#d9c9a8"/>
          <stop offset="1" stop-color="#f1efe9"/>
        </linearGradient>
      </defs>
      <rect width="360" height="700" fill="url(#coverPhoto)" role="img" aria-label="Photo of a senior golden retriever lying in the grass"/>
      <path d="M0 312Q180 300 360 290V520Q180 512 0 528Z" fill="var(--teal-soft)" aria-hidden="true"/>
    </svg>
    <div class="brand-box">
      <span class="brand-dot"></span>
      <span class="brand-name">Trellis Animal Respite &amp; Home Care</span>
    </div>
    <p class="tagline">Skilled Home Care for Ill,<br>Elderly and Special Needs Animals</p>
    <p class="script-line">Compassionate Support<br>for Families</p>
  </section>

</main>
</body>
</html>
```